Structural Engineering Business Card

Brookvane Drafting does residential house plans for clients in Central Florida. Would like simple but elegant business card that is appropriate for a house plan engineering company. Prefer black business card with black/white them but open to other shades of blue. I uploaded a sample card that I came across that looked good but please come up with your own creative designs.

Contact Information for Business Card

Name, Title, Phone, Email, Address, website

```html
<!DOCTYPE html>
<html lang="en">
<head>
<meta charset="utf-8">
<title>Brookvane Drafting — Business Card</title>
<link href="https://fonts.googleapis.com/css2?family=Montserrat:wght@400;700;800&display=swap" rel="stylesheet">
<style>
  :root {
    --bg: #2b2d31;
    --navy: #25286e;
    --navy-mid: #1d4a7e;
    --teal: #0b8a8c;
    --white: #ffffff;
    --soft: rgba(255,255,255,0.78);
    --line: rgba(255,255,255,0.55);
  }
  * { box-sizing: border-box; margin: 0; padding: 0; }
  html, body { width: 1200px; height: 817px; overflow: hidden; }
  body {
    background: var(--bg);
    font-family: "Montserrat", Arial, sans-serif;
    color: var(--white);
    position: relative;
  }
  .card {
    position: absolute;
    top: 254px;
    width: 540px;
    height: 309px;
    border-radius: 28px;
    overflow: hidden;
    box-shadow: 0 18px 40px rgba(0,0,0,0.45);
  }
  .card--front {
    left: 40px;
    background: linear-gradient(35deg, var(--teal) 0%, var(--navy-mid) 55%, var(--navy) 100%);
  }
  .card--back {
    left: 620px;
    background: linear-gradient(215deg, var(--teal) 0%, var(--navy-mid) 45%, var(--navy) 85%);
  }
  .blueprint-area {
    position: absolute;
    background: linear-gradient(200deg, rgba(255,255,255,0.10), rgba(255,255,255,0.02));
  }
  .card--front .blueprint-area { right: 0; top: 0; width: 300px; height: 230px; }
  .card--back .blueprint-area { right: 0; top: 70px; width: 300px; height: 239px; }
  .brand {
    position: absolute;
    display: flex;
    align-items: center;
    gap: 10px;
    font-weight: 800;
    text-transform: uppercase;
    letter-spacing: 1px;
    color: var(--white);
  }
  .brand__mark { width: 14px; height: 14px; background: var(--white); }
  .card--front .brand { left: 0; right: 0; top: 138px; justify-content: center; font-size: 26px; }
  .card--back .brand { right: 28px; top: 30px; font-size: 20px; }
  .person { position: absolute; left: 36px; top: 92px; }
  .person__name { font-size: 17px; font-weight: 700; letter-spacing: 0.6px; text-transform: uppercase; }
  .person__title { font-size: 13px; font-weight: 400; color: var(--soft); margin-top: 3px; }
  .person__rule { width: 70px; height: 1px; background: var(--line); margin-top: 8px; }
  .contacts { position: absolute; left: 36px; top: 178px; list-style: none; }
  .contacts li { display: flex; align-items: flex-start; gap: 9px; font-size: 11.5px; line-height: 1.3; margin-bottom: 7px; }
  .contacts svg { width: 15px; height: 15px; flex: none; }
</style>
</head>
<body>
  <section class="card card--front">
    <div class="blueprint-area" role="img" aria-label="Faint blueprint line drawing of a house elevation"></div>
    <div class="brand"><span class="brand__mark"></span>Brookvane Drafting</div>
  </section>

  <section class="card card--back">
    <div class="blueprint-area" role="img" aria-label="Faint blueprint line drawing of a house elevation"></div>
    <div class="brand"><span class="brand__mark"></span>Brookvane Drafting</div>

    <div class="person">
      <h1 class="person__name">Dana M. Whitlock</h1>
      <p class="person__title">Managing Director</p>
      <div class="person__rule"></div>
    </div>

    <ul class="contacts">
      <li>
        <svg viewBox="0 0 16 16"><rect width="16" height="16" rx="2" fill="#fff"/><path d="M8 3a3.5 3.5 0 0 0-3.5 3.5C4.5 9.5 8 13 8 13s3.5-3.5 3.5-6.5A3.5 3.5 0 0 0 8 3zm0 4.8a1.3 1.3 0 1 1 0-2.6 1.3 1.3 0 0 1 0 2.6z" fill="#25286e"/></svg>
        <span>1420 Lakeshore Avenue<br>Florida, U.S. 32801</span>
      </li>
      <li>
        <svg viewBox="0 0 16 16"><rect width="16" height="16" rx="2" fill="#fff"/><path d="M5 3.5l2 2-1.2 1.4c.7 1.4 1.9 2.6 3.3 3.3L10.5 9l2 2-1.3 1.5C7.5 12.3 3.7 8.5 3.5 4.8z" fill="#25286e"/></svg>
        <span>+1 407 555 0182</span>
      </li>
      <li>
        <svg viewBox="0 0 16 16"><rect width="16" height="16" rx="2" fill="#fff"/><rect x="3" y="4.5" width="10" height="7" fill="none" stroke="#25286e" stroke-width="1.3"/><path d="M3 4.5l5 4 5-4" fill="none" stroke="#25286e" stroke-width="1.3"/></svg>
        <span>hello@brookvanedrafting.com</span>
      </li>
      <li>
        <svg viewBox="0 0 16 16"><rect width="16" height="16" rx="2" fill="#fff"/><path d="M4.5 4.5l7 3-3 1 -1 3z" fill="#25286e"/></svg>
        <span>www.brookvanedrafting.com</span>
      </li>
    </ul>
  </section>
</body>
</html>
```